Brindle Water - 500ml

to create a water bottle packaging similar to L'onde Claire design. Bottle should be blue similar to PURE FLOW but change the design/logo to Brindle. Wording should be similar just different design and logo. Thanks.

Colors
0054AA
0677BA
7BADD7
CADEEF
E8F1F8

Requirements
Must have
• Bottle must not be in plastic bottles. They are made in a carton instead - see PURE FLOW for reference.

```html
<!DOCTYPE html>
<html lang="en">
<head>
<meta charset="utf-8">
<title>Brindle Water – 500ml Carton</title>
<link href="https://fonts.googleapis.com/css2?family=Oswald:wght@500;600;700&family=Roboto+Condensed:wght@400;700&display=swap" rel="stylesheet">
<style>
  :root {
    --navy: #0054AA;
    --carton: #0677BA;
    --carton-bright: #1b95d3;
    --carton-shade: #0b6aa6;
    --sky: #7BADD7;
    --mist: #CADEEF;
    --ice: #E8F1F8;
    --white: #ffffff;
    --stage: #f3f5f7;
  }
  * { box-sizing: border-box; margin: 0; padding: 0; }
  html, body { width: 1200px; height: 3000px; overflow: hidden; }
  body {
    background: var(--stage);
    position: relative;
    font-family: "Roboto Condensed", "Arial Narrow", sans-serif;
    color: var(--white);
  }
  .carton { position: absolute; }
  .carton-roof { display: block; }
  .carton-body {
    position: absolute;
    left: 0; right: 0; bottom: 0;
    background: linear-gradient(90deg, var(--carton-bright) 0%, #27a2dc 55%, var(--carton-bright) 100%);
  }

  /* ---------- side panel ---------- */
  .panel-side { left: 110px; top: 90px; width: 440px; height: 1200px; }
  .panel-side .carton-body { top: 220px; }
  .benefit-list {
    list-style: none;
    position: absolute; left: 0; right: 0; top: 50px;
    display: flex; flex-direction: column; align-items: center; gap: 34px;
  }
  .benefit { display: flex; flex-direction: column; align-items: center; gap: 10px; }
  .benefit svg { width: 64px; height: 64px; }
  .benefit-label {
    font-family: "Oswald", sans-serif; font-weight: 500;
    font-size: 15px; letter-spacing: 1.5px;
  }
  .side-note {
    position: absolute; left: 0; right: 0; bottom: 40px;
    text-align: center; font-size: 14px; letter-spacing: 1px; color: var(--ice);
  }

  /* ---------- back panel ---------- */
  .panel-back { left: 650px; top: 90px; width: 440px; height: 1200px; }
  .panel-back .carton-body { top: 220px; padding: 40px 46px 0; }
  .roof-name {
    position: absolute; left: 0; right: 0; top: 120px;
    text-align: center; font-family: "Oswald", sans-serif; font-weight: 600;
    font-size: 40px; color: var(--white);
  }
  .badge {
    width: 110px; height: 110px; border-radius: 50%;
    border: 4px solid var(--white); margin: 0 auto 36px;
  }
  .section-title {
    font-family: "Oswald", sans-serif; font-weight: 600;
    font-size: 18px; letter-spacing: 1.5px; margin-bottom: 10px;
  }
  .facts { width: 100%; border-collapse: collapse; margin-bottom: 30px; font-size: 15px; }
  .facts td { padding: 4px 0; border-bottom: 1px solid rgba(255,255,255,.45); }
  .facts td:last-child { text-align: right; }
  .pledge {
    font-family: "Oswald", sans-serif; font-weight: 700;
    font-size: 22px; letter-spacing: 1px; margin-bottom: 8px;
  }
  .pledge-text { font-size: 15px; line-height: 1.4; color: var(--ice); margin-bottom: 30px; }
  .date-box {
    border: 2px solid var(--white); padding: 14px;
    font-size: 14px; letter-spacing: 1px; text-align: center;
  }

  /* ---------- front panel ---------- */
  .panel-front { left: 300px; top: 1420px; width: 600px; height: 1500px; }
  .panel-front .carton-body { top: 260px; }
  .brand-box {
    position: absolute; left: 300px; top: 60px; width: 230px; height: 120px;
    background: var(--white); color: var(--carton);
    display: flex; flex-direction: column; align-items: center; justify-content: center;
  }
  .brand-name { font-family: "Oswald", sans-serif; font-weight: 600; font-size: 56px; line-height: 1; }
  .brand-tag { font-size: 12px; letter-spacing: 2px; margin-top: 6px; }
  .product-word {
    position: absolute; left: 415px; top: 590px;
    transform: translate(-50%, -50%) rotate(-90deg);
    font-family: "Oswald", sans-serif; font-weight: 700;
    font-size: 250px; line-height: 1; letter-spacing: 4px; white-space: nowrap;
  }
  .product-info {
    position: absolute; left: 235px; width: 360px; top: 975px;
    text-align: center;
  }
  .product-claim {
    font-family: "Oswald", sans-serif; font-weight: 600;
    font-size: 40px; line-height: 1.1; letter-spacing: 1px;
  }
  .product-desc { font-size: 17px; font-weight: 700; letter-spacing: 1px; line-height: 1.35; margin-top: 26px; }
  .product-volume { font-size: 16px; font-weight: 700; letter-spacing: 2px; margin-top: 30px; }
</style>
</head>
<body>

  <!-- side panel -->
  <section class="carton panel-side" aria-label="Carton side panel">
    <svg class="carton-roof" width="440" height="220" viewBox="0 0 440 220">
      <rect x="0" y="20" width="440" height="200" fill="#1a8fcb"/>
      <polygon points="220,20 0,220 440,220" fill="#27a2dc"/>
      <line x1="220" y1="20" x2="0" y2="220" stroke="#0b6aa6" stroke-width="2"/>
      <line x1="220" y1="20" x2="440" y2="220" stroke="#0b6aa6" stroke-width="2"/>
      <rect x="200" y="0" width="40" height="22" fill="#1583c0"/>
    </svg>
    <div class="carton-body">
      <ul class="benefit-list">
        <li class="benefit">
          <svg viewBox="0 0 64 64" fill="none" stroke="#fff" stroke-width="3"><path d="M14 50 C14 24 32 12 52 12 C52 34 40 50 14 50 Z"/><path d="M14 50 L38 26"/></svg>
          <span class="benefit-label">PLANT-BASED CARTON</span>
        </li>
        <li class="benefit">
          <svg viewBox="0 0 64 64" fill="none" stroke="#fff" stroke-width="3"><path d="M20 22 A18 18 0 0 1 50 30"/><path d="M44 42 A18 18 0 0 1 14 34"/><path d="M44 24 L50 30 L54 22"/><path d="M20 40 L14 34 L10 42"/></svg>
          <span class="benefit-label">FULLY RECYCLABLE</span>
        </li>
        <li class="benefit">
          <svg viewBox="0 0 64 64" fill="none" stroke="#fff" stroke-width="3"><path d="M32 8 C22 24 16 32 16 40 A16 16 0 0 0 48 40 C48 32 42 24 32 8 Z"/></svg>
          <span class="benefit-label">NATURALLY FILTERED</span>
        </li>
        <li class="benefit">
          <svg viewBox="0 0 64 64" fill="none" stroke="#fff" stroke-width="3"><path d="M6 52 L24 22 L34 36 L42 26 L58 52 Z"/></svg>
          <span class="benefit-label">SOURCED IN THE HILLS</span>
        </li>
        <li class="benefit">
          <svg viewBox="0 0 64 64" fill="none" stroke="#fff" stroke-width="3"><circle cx="32" cy="32" r="24"/><path d="M20 33 L29 42 L45 24"/></svg>
          <span class="benefit-label">LOW CARBON FOOTPRINT</span>
        </li>
        <li class="benefit">
          <svg viewBox="0 0 64 64" fill="none" stroke="#fff" stroke-width="3"><path d="M10 32 L50 32"/><path d="M38 20 L50 32 L38 44"/></svg>
          <span class="benefit-label">RETURN TO RECYCLE</span>
        </li>
      </ul>
      <p class="side-note">STORE IN A COOL DRY PLACE</p>
    </div>
  </section>

  <!-- back panel -->
  <section class="carton panel-back" aria-label="Carton back panel">
    <svg class="carton-roof" width="440" height="220" viewBox="0 0 440 220">
      <rect x="10" y="0" width="420" height="24" fill="#1583c0"/>
      <rect x="0" y="24" width="440" height="196" fill="#1a8fcb"/>
    </svg>
    <p class="roof-name">Brindle</p>
    <div class="carton-body">
      <div class="badge"></div>
      <h3 class="section-title">TYPICAL WATER ANALYSIS MG/L</h3>
      <table class="facts">
        <tr><td>CALCIUM</td><td>12.0</td></tr>
        <tr><td>MAGNESIUM</td><td>4.2</td></tr>
        <tr><td>POTASSIUM</td><td>1.1</td></tr>
        <tr><td>SODIUM</td><td>8.5</td></tr>
        <tr><td>NITRATE</td><td>2.0</td></tr>
        <tr><td>PH</td><td>7.2</td></tr>
      </table>
      <p class="pledge">GOOD FOR YOU &amp; THE PLANET</p>
      <p class="pledge-text">CARTON MADE FROM RENEWABLE MATERIALS, PLEASE FLATTEN AND RECYCLE</p>
      <h3 class="section-title">PACKAGING FACTS</h3>
      <table class="facts">
        <tr><td>PAPERBOARD</td><td>75%</td></tr>
        <tr><td>PLANT POLYMER</td><td>20%</td></tr>
        <tr><td>ALUMINIUM</td><td>5%</td></tr>
      </table>
      <div class="date-box">BEST BEFORE SEE TOP OF CARTON</div>
    </div>
  </section>

  <!-- front panel -->
  <section class="carton panel-front" aria-label="Carton front panel">
    <svg class="carton-roof" width="600" height="260" viewBox="0 0 600 260">
      <defs>
        <linearGradient id="roofShade" x1="0" y1="0" x2="0" y2="1">
          <stop offset="0" stop-color="#1583c0"/>
          <stop offset="1" stop-color="#1f97d4"/>
        </linearGradient>
        <linearGradient id="capSide" x1="0" y1="0" x2="1" y2="0">
          <stop offset="0" stop-color="#1a8fcb"/>
          <stop offset="0.5" stop-color="#3aaee3"/>
          <stop offset="1" stop-color="#1583c0"/>
        </linearGradient>
      </defs>
      <rect x="14" y="0" width="572" height="30" fill="#1583c0"/>
      <rect x="0" y="30" width="600" height="230" fill="url(#roofShade)"/>
      <line x1="0" y1="258" x2="600" y2="258" stroke="#0b6aa6" stroke-width="3"/>
      <rect x="180" y="110" width="180" height="90" rx="8" fill="url(#capSide)"/>
      <ellipse cx="270" cy="110" rx="90" ry="26" fill="#3cb0e5"/>
      <ellipse cx="270" cy="110" rx="72" ry="19" fill="none" stroke="#1a8fcb" stroke-width="3"/>
    </svg>
    <div class="carton-body">
      <div class="brand-box">
        <span class="brand-name">Brindle</span>
        <span class="brand-tag">SOURCED AT THE SPRING</span>
      </div>
      <h1 class="product-word">WATER</h1>
      <div class="product-info">
        <p class="product-claim">100%<br>SPRING WATER</p>
        <p class="product-desc">SUSTAINABLY SOURCED WATER<br>IN A PLANT-BASED<br>CARTON</p>
        <p class="product-volume">500ML</p>
      </div>
    </div>
  </section>

</body>
</html>
```